Local Flower Farm Needs Business Card Design

I need business cards designed for a flower farm based in Eudora, Kansas.
Business Info:
We are a local cut flower farm located in Eudora, Kansas, founded by Corinne Haldwick. What started as a passion for agriculture and search for more joy in daily life has blossomed into a small business dedicated to providing the community with beautiful, fresh, and sustainable flowers. We specialize in local, seasonal blooms, ensuring that every petal reflects the care and dedication we pour into our craft. Our mission is to deliver the highest quality flowers directly to our customers through local farmers markets and to florists who share our commitment to sustainability. Join us in celebrating the beauty of nature, one bloom at a time!
Contact Details:
Corinne Haldwick
Owner
Phone 913-555-0147
Facebook: Rosalind Thorpe Gardens
Instagram: @RosalindThorpeGardens
Website: RosalindThorpeGardens.example
Target Market(s)
Wholesale to Florists and Direct to Consumer via Farmers Market
Industry/Entity Type
Florist, Farm
Contact Information for Business Card
Name, Contact Info, Logo
Look and feel
Each slider illustrates characteristics of the customer's brand and the style your logo design should communicate.

```html
<!DOCTYPE html>
<html lang="en">
<head>
<meta charset="utf-8">
<title>Rosalind Thorpe Gardens – Business Card</title>
<link href="https://fonts.googleapis.com/css2?family=Montserrat:wght@400;500;700&display=swap" rel="stylesheet">
<style>
  :root {
    --ink: #0d2a2e;
    --ring: #5d6466;
    --card: #ffffff;
    --backdrop: #9b9b9b;
  }
  * { margin: 0; padding: 0; box-sizing: border-box; }
  html, body {
    width: 1093px;
    height: 1200px;
    overflow: hidden;
    background: var(--backdrop);
    font-family: "Montserrat", Arial, sans-serif;
    color: var(--ink);
  }
  .canvas { position: relative; width: 1093px; height: 1200px; }
  .card {
    position: absolute;
    left: 264px;
    width: 597px;
    background: var(--card);
    border-radius: 18px;
    overflow: hidden;
  }
  .card--front { top: 225px; height: 363px; }
  .card--back { top: 616px; height: 366px; }

  .holder { position: absolute; left: 30px; top: 44px; }
  .holder__name { font-size: 22px; font-weight: 700; line-height: 1.1; letter-spacing: -0.1px; }
  .holder__role { font-size: 13.5px; font-weight: 400; margin-top: 2px; }

  .brand-mark {
    position: absolute;
    display: flex;
    align-items: center;
    justify-content: center;
    text-align: center;
    border: 1px solid var(--ring);
    border-radius: 50%;
    color: var(--ink);
    font-weight: 700;
    line-height: 1.15;
  }
  .brand-mark--small { left: 426px; top: 33px; width: 128px; height: 128px; font-size: 14px; padding: 14px; }
  .brand-mark--large { left: 171px; top: 69px; width: 256px; height: 256px; font-size: 28px; padding: 28px; }

  .contacts { position: absolute; left: 30px; top: 252px; list-style: none; }
  .contacts__item {
    display: flex;
    align-items: center;
    height: 21.7px;
    font-size: 13.6px;
    font-weight: 400;
    white-space: nowrap;
  }
  .contacts__icon { width: 13px; height: 13px; margin-right: 7px; flex: none; }

  .address {
    position: absolute;
    left: 406px;
    top: 301px;
    font-size: 13.6px;
    line-height: 17px;
    font-style: normal;
    white-space: nowrap;
  }
</style>
</head>
<body>
<main class="canvas">

  <section class="card card--front" aria-label="Business card front">
    <header class="holder">
      <h1 class="holder__name">Corinne Haldwick</h1>
      <p class="holder__role">Owner</p>
    </header>

    <div class="brand-mark brand-mark--small">Rosalind Thorpe Gardens</div>

    <ul class="contacts">
      <li class="contacts__item">
        <svg class="contacts__icon" viewBox="0 0 16 16" aria-hidden="true">
          <path fill="var(--ink)" d="M3.6 1.2l2.3 2.6-1.3 1.8c.8 2 2.3 3.6 4.3 4.5l1.8-1.3 2.6 2.3-1.4 2.4C6.6 13.3 2.7 9.4 1.2 4.1z"/>
          <path fill="none" stroke="var(--ink)" stroke-width="1.2" d="M9.5 2.2a4.5 4.5 0 0 1 4.3 4.3M9.3 4.6a2.2 2.2 0 0 1 2.1 2.1"/>
        </svg>
        913-555-0147
      </li>
      <li class="contacts__item">
        <svg class="contacts__icon" viewBox="0 0 16 16" aria-hidden="true"><circle cx="8" cy="8" r="7.5" fill="var(--ink)"/></svg>
        Rosalind Thorpe Gardens
      </li>
      <li class="contacts__item">
        <svg class="contacts__icon" viewBox="0 0 16 16" aria-hidden="true"><circle cx="8" cy="8" r="7.5" fill="var(--ink)"/></svg>
        @RosalindThorpeGardens
      </li>
      <li class="contacts__item">
        <svg class="contacts__icon" viewBox="0 0 16 16" aria-hidden="true">
          <circle cx="8" cy="8" r="7" fill="none" stroke="var(--ink)" stroke-width="1.4"/>
          <ellipse cx="8" cy="8" rx="3" ry="7" fill="none" stroke="var(--ink)" stroke-width="1.2"/>
          <path d="M1 8h14" stroke="var(--ink)" stroke-width="1.2"/>
        </svg>
        www.RosalindThorpeGardens.example
      </li>
    </ul>

    <address class="address">
      418 Meadowlark Rd, #12<br>
      Eudora, KS 66025
    </address>
  </section>

  <section class="card card--back" aria-label="Business card back">
    <div class="brand-mark brand-mark--large">Rosalind Thorpe Gardens</div>
  </section>

</main>
</body>
</html>
```